Corporate Travel Technology Company needs new Business Card design

We need a new business card design to reflect our re-branded company. Our company is called tolvEn (pronounced tolvenn) and we provide Business Intelligence and mobile travel management solutions for the corporate travel industry. Our multinational customers use our solutions to manage large travel budgets and frequent travellers, as well as to save money and reduce risk. We'd like to see designs that use the blue and green palette as well as our corporate logo (attached below). The design should communicate innovation, insight, forward thinking, contemporary, trusted.

Target Market(s)

Large multinational corporates and Travel Agencies.

Industry/Entity Type

Business

Contact Information for Business Card

Rosalind Mercer
Chief Executive
tolvEn
Phone number - +61 (0)2 8134 2907
Email address - rosalind.mercer@tolven-example.com
Mobile number - +61 (0)438 516 702
www.tolven-example.com

Font styles to use
Other font styles liked:
• Please use font as close to corporate logo as possible

Colors
0255a3
0393ce
00a990
33b8a4
33a6d7
3176b5

Requirements
Must have
• Please include the words;
• Mobile Travel Management
• Accelerating Travel Business Insights
• Use corporate logo - although icon can be stylised if needed

```html
<!DOCTYPE html>
<html lang="en">
<head>
<meta charset="UTF-8">
<title>tolven Business Card</title>
<link rel="stylesheet" href="https://fonts.googleapis.com/css2?family=Open+Sans:wght@400;600&display=swap">
<style>
  :root {
    --backdrop: #3a3431;
    --card: #0b0b0c;
    --card-edge: #1c1c1e;
    --accent-blue: #2ea6dd;
    --divider: #1f4a5e;
    --text-light: #e4e4e4;
    --text-soft: #cfcfcf;
    --wordmark: #8f9a9c;
    --silver: #c9c9cb;
  }
  * { margin: 0; padding: 0; box-sizing: border-box; }
  html, body {
    width: 1200px;
    height: 900px;
    overflow: hidden;
    background: var(--backdrop);
    font-family: "Open Sans", Arial, sans-serif;
  }
  .stage {
    position: relative;
    width: 1200px;
    height: 900px;
  }
  .card {
    position: absolute;
    top: 290px;
    width: 540px;
    height: 310px;
    background: var(--card);
    border: 1px solid var(--card-edge);
    box-shadow: 0 10px 28px rgba(0,0,0,0.45);
  }
  .card-front { left: 40px; }
  .card-back { left: 620px; }

  /* Front */
  .brand-name {
    position: absolute;
    left: 40px;
    top: 160px;
    font-size: 50px;
    font-weight: 400;
    color: var(--wordmark);
    line-height: 1;
    white-space: nowrap;
  }
  .divider {
    position: absolute;
    left: 262px;
    top: 72px;
    width: 1px;
    height: 160px;
    background: var(--divider);
  }
  .contact {
    position: absolute;
    left: 278px;
    top: 66px;
    white-space: nowrap;
  }
  .person-name {
    font-size: 17px;
    font-weight: 600;
    color: var(--accent-blue);
    line-height: 1.3;
  }
  .person-title {
    font-size: 12.5px;
    color: var(--text-soft);
    margin-bottom: 18px;
  }
  .contact-list { list-style: none; }
  .contact-item {
    display: flex;
    align-items: center;
    gap: 10px;
    font-size: 12.5px;
    color: var(--text-light);
    line-height: 1.6;
  }
  .contact-icon {
    width: 10px;
    height: 10px;
    flex: none;
    fill: var(--accent-blue);
  }

  /* Back */
  .back-name {
    position: absolute;
    left: 0;
    right: 0;
    top: 100px;
    text-align: center;
    font-size: 44px;
    font-weight: 400;
    color: var(--silver);
    line-height: 1;
  }
  .taglines {
    position: absolute;
    left: 0;
    right: 0;
    top: 222px;
    text-align: center;
    color: var(--text-light);
    font-size: 13px;
    line-height: 1.5;
  }
</style>
</head>
<body>
<main class="stage">
  <section class="card card-front">
    <span class="brand-name">tolven</span>
    <div class="divider"></div>
    <div class="contact">
      <p class="person-name">Rosalind Mercer</p>
      <p class="person-title">Chief Executive</p>
      <ul class="contact-list">
        <li class="contact-item">
          <svg class="contact-icon" viewBox="0 0 10 10"><path d="M2 0.5 L3.6 2.6 L2.7 3.6 Q3.6 5.8 6.4 7.3 L7.4 6.4 L9.5 8 L8.2 9.5 Q1.5 8 0.5 1.8 Z"/></svg>
          <span>+61 (0)2 8134 2907</span>
        </li>
        <li class="contact-item">
          <svg class="contact-icon" viewBox="0 0 10 10"><path d="M2.5 0 H7.5 V10 H2.5 Z M3.4 1 V8 H6.6 V1 Z" fill-rule="evenodd"/></svg>
          <span>+61 (0)438 516 702</span>
        </li>
        <li class="contact-item">
          <svg class="contact-icon" viewBox="0 0 10 10"><path d="M0.5 2 H9.5 V8.5 H0.5 Z M1.3 2.6 L5 5.4 L8.7 2.6 Z" fill-rule="evenodd"/></svg>
          <span>rosalind.mercer@tolven-example.com</span>
        </li>
        <li class="contact-item">
          <svg class="contact-icon" viewBox="0 0 10 10"><circle cx="5" cy="5" r="4.6"/></svg>
          <span>www.tolven-example.com</span>
        </li>
      </ul>
    </div>
  </section>

  <section class="card card-back">
    <p class="back-name">tolven</p>
    <div class="taglines">
      <p>Mobile Travel Management</p>
      <p>Accelerating Travel Business Insights</p>
    </div>
  </section>
</main>
</body>
</html>
```